South Florida Real Estate Brokerage Business

The name is LAKE VORISSA REAL ESTATE.
The company is a Real estate realty based in Miami.
Is targeted to Latin American clients.
Must express luxury, and efficiency.
Target clients for properties around 250k to a million +.
Vorissa means Royal in Latin.
Should communicate safety and knowledge of the product and transaction with a tech edge.

The web design needs to be a Social tool, with Friendloop and other media integration of some sort. Needs to have a Show case place, a Search place (MLS listings) with maps and filters.
Needs to reflect luxury but also mixed with a social edge capable of engaging clients or transition them to communicate with the page.
Include the logo from the uploaded files, feel free to change the color or font per webdesign.
This is a Front en design, layout and graphics.
Possible future programming if approved.
I can receive Quotes for the Code part.

Spanish and English speakers living in Latin America and Canada looking for apartments and houses to buy.

Business

• Search area.
Neighbourhood area.
Could be a blog or news area.
Client registration.
Social Plugin
• Social linking to networks.
Log in with friendloop account.
Friendloop Like.

```html
<!DOCTYPE html>
<html lang="en">
<head>
<meta charset="utf-8">
<title>Lake Vorissa Real Estate</title>
<link href="https://fonts.googleapis.com/css2?family=Cinzel:wght@500&family=Roboto+Condensed:wght@400&family=Arimo:ital,wght@0,400;0,700;1,400;1,700&display=swap" rel="stylesheet">
<style>
:root{
  --cream:#efebe2;
  --gold:#c2a96b;
  --gold-dark:#7d6a3f;
  --brown:#4c402a;
  --panel:#7b6a45;
  --panel-dark:#5a4b2e;
  --sand:#b6a282;
  --sand-light:#e2d8c2;
  --footer:#2f2b25;
  --footer-dark:#1e1b17;
  --ink:#2d2a24;
  --muted:#d9d2c4;
  --white:#ffffff;
  --orange:#e0621e;
}
*{box-sizing:border-box;margin:0;padding:0}
html,body{width:865px;height:1200px;overflow:hidden}
body{position:relative;background:var(--cream);font-family:"Arimo",Arial,sans-serif;color:var(--ink)}
.abs{position:absolute}
.header{left:0;top:0;width:865px;height:442px;background:var(--cream)}
.brand{left:110px;top:8px;width:150px;text-align:center}
.brand-mark{width:50px;height:50px;background:var(--gold);margin:0 auto 8px}
.brand-name{font-family:"Cinzel",serif;font-weight:500;font-size:15px;line-height:17px;color:var(--ink);letter-spacing:.5px}
.keyword{left:409px;top:9px;width:162px;height:20px;background:#d9ceb3;font-size:9px;color:#6b614e;padding:5px 8px}
.keyword svg{position:absolute;right:2px;top:-2px}
.likes{left:598px;top:8px;font-size:8px;color:#6b614e;display:flex;align-items:center;gap:6px}
.likes i{display:block;width:18px;height:16px;background:#9aa9c4;border-radius:2px}
.fl-signin{left:661px;top:9px;width:101px;height:17px;border-radius:9px;background:linear-gradient(#6f8fd0,#3f62aa);color:var(--white);font-size:7.5px;font-weight:700;text-align:center;line-height:17px}
.btn{height:21px;background:var(--gold-dark);color:#f3ead6;font-size:10px;text-align:center;line-height:21px;border-radius:2px}
.nav{left:117px;top:111px;width:633px;height:29px;background:linear-gradient(#cdb47a,#b79c5c);display:flex;align-items:center;font-family:"Roboto Condensed",sans-serif;font-size:14px;color:var(--white);border-radius:2px}
.nav span{position:absolute;top:7px}
.hero-frame{left:110px;top:148px;width:394px;height:281px;background:var(--brown);border-radius:5px;box-shadow:0 6px 10px rgba(0,0,0,.3)}
.hero-photo{left:117px;top:155px;width:379px;height:265px;background:linear-gradient(#6f9bd2 0%,#b8cde6 38%,#d8d8d4 40%,#a9aba6 75%,#4b5743 100%);border-radius:3px}
.listings{left:503px;top:155px;width:252px;height:265px;background:var(--panel);border-radius:0 5px 5px 0;box-shadow:0 6px 10px rgba(0,0,0,.3)}
.listing{position:absolute;left:0;width:252px;height:76px;font-size:8px;color:#efe6cf}
.listing.active{background:var(--panel-dark)}
.listing .thumb{position:absolute;left:16px;top:10px;width:62px;height:56px;border:1px solid #d8ccaa}
.listing .c1{position:absolute;left:97px}
.listing .c2{position:absolute;left:164px}
.badge{left:433px;top:355px;width:78px;height:78px;border-radius:50%;background:radial-gradient(#f08a3c,var(--orange));color:var(--white);font-family:"Arimo",sans-serif;font-style:italic;font-weight:700;font-size:13px;text-align:center;line-height:14px;padding-top:24px;transform:rotate(-12deg);box-shadow:0 2px 4px rgba(0,0,0,.35)}
.search-band{left:0;top:445px;width:865px;height:118px;background:linear-gradient(var(--sand-light),#d8ccb0);box-shadow:0 -2px 4px rgba(0,0,0,.15)}
.search-map{left:112px;top:453px;width:143px;height:62px;background:linear-gradient(120deg,#2f5a78,#6d8f6a 55%,#2e5674);border:3px solid #f4f0e6;transform:skewY(-3deg);box-shadow:0 2px 4px rgba(0,0,0,.3)}
.search-panel{left:140px;top:472px;width:605px;height:75px;background:#ddd2b7;box-shadow:0 2px 5px rgba(0,0,0,.25);border-radius:3px}
.search-title{left:263px;top:477px;font-size:11px;color:#2b281f}
.select{top:495px;width:108px;height:22px;background:linear-gradient(#e8e1cf,#c7bb9c);border:1px solid #9b8d6c;border-radius:2px;font-size:8px;color:#4a4332;padding:6px 6px}
.select::after{content:"";position:absolute;right:6px;top:7px;border:5px solid transparent;border-top:7px solid #6e6450}
.showcase{left:0;top:563px;width:865px;height:402px;background:var(--sand)}
.section-title{left:0;top:585px;width:865px;text-align:center;font-style:italic;font-size:13px;color:var(--white)}
.rule{left:100px;top:606px;width:670px;height:1px;background:#cdbf9f}
.work{top:628px;height:108px}
.work .cap{position:absolute;left:0;bottom:0;width:100%;height:28px;background:rgba(40,35,25,.55);color:var(--white);font-size:8px;line-height:11px;padding:4px 10px}
.pager{left:310px;top:750px;font-size:9px;color:#4e4432;word-spacing:14px}
.pager-rule{left:100px;top:768px;width:670px;height:2px;background:linear-gradient(90deg,transparent,#8f7e5d,transparent)}
.col{top:793px;width:202px}
.col h2{font-style:italic;font-weight:400;font-size:12px;color:#2e2a22;margin-bottom:8px}
.col h2 b{font-weight:400;color:var(--white);font-size:13px}
.col p{font-size:8px;line-height:11.5px;color:var(--white);text-align:justify}
.col .more{display:block;text-align:right;color:#2e2a22;font-size:7.5px;margin-top:-10px;margin-bottom:8px}
.col .lead{color:#111;font-weight:700;font-style:italic;margin-top:8px}
.divider{top:795px;width:2px;height:125px;background:linear-gradient(#8a7a58,transparent)}
.footer{left:0;top:965px;width:865px;height:190px;background:var(--footer)}
.foot-title{font-size:10px;color:var(--white)}
.features{left:110px;top:987px;width:203px}
.features .foot-title{border-bottom:1px solid #6b6558;padding-bottom:2px;margin-bottom:10px}
.features li{list-style:none;font-size:8px;color:var(--muted);height:19px;padding-left:8px;position:relative}
.features li::before{content:"";position:absolute;left:0;top:2px;border:3px solid transparent;border-left:4px solid var(--orange)}
.vline{top:990px;width:1px;height:140px;background:#57524a}
.offices{left:390px;top:986px}
.office-map{left:390px;top:1006px;width:158px;height:60px;background:linear-gradient(#c8c8c8,#8c8c8c);border-radius:4px}
.places{font-size:8.5px;color:var(--muted);line-height:16px}
.places li{list-style:none;padding-left:9px;position:relative}
.places li::before{content:"";position:absolute;left:0;top:5px;border:3px solid transparent;border-left:4px solid var(--orange)}
.social{left:613px;width:128px;height:28px;font-size:8.5px;color:var(--muted);line-height:10px;border-bottom:1px solid #57524a}
.social i{position:absolute;left:0;top:0;width:22px;height:22px;border-radius:50%}
.social span{position:absolute;left:40px;top:6px}
.social span.two{top:1px}
.bottom{left:0;top:1153px;width:865px;height:47px;background:var(--footer-dark)}
.bottom-links{left:110px;top:1172px;font-size:7.5px;color:#a9a398}
.copyright{left:668px;top:1171px;font-size:7px;color:#a9a398}
</style>
</head>
<body>

<header class="abs header"></header>
<div class="abs brand">
  <div class="brand-mark"></div>
  <div class="brand-name">LAKE VORISSA<br>REAL ESTATE</div>
</div>
<div class="abs keyword">Enter your keyword
  <svg width="24" height="24" viewBox="0 0 24 24"><circle cx="10" cy="10" r="6" fill="#f2f2f2" stroke="#777" stroke-width="2"/><line x1="14" y1="14" x2="21" y2="21" stroke="#e08b1e" stroke-width="3"/></svg>
</div>
<div class="abs likes"><i></i>240 likes</div>
<div class="abs fl-signin">Sign in with Friendloop</div>
<div class="abs btn" style="left:579px;top:80px;width:65px">Sign In</div>
<div class="abs btn" style="left:651px;top:80px;width:98px">Client Registration</div>

<nav class="abs nav">
  <span style="left:23px">HOME</span>
  <span style="left:87px">COMPANY</span>
  <span style="left:164px">ASSOCIATES</span>
  <span style="left:262px">SEARCH PROPERTIES</span>
  <span style="left:401px">MARKETING &amp; DESIGN</span>
  <span style="left:550px">CONTACT</span>
</nav>

<div class="abs hero-frame"></div>
<div class="abs hero-photo" role="img" aria-label="Featured property photo: modern office building with glass windows"></div>
<div class="abs listings">
  <div class="listing active" style="top:18px">
    <div class="thumb" role="img" aria-label="Villa photo" style="background:linear-gradient(#7fa8d6,#d0d0cc 60%,#5d6a4a)"></div>
    <span class="c1" style="top:15px">Villa</span><span class="c2" style="top:15px">Information 1</span>
    <span class="c1" style="top:33px">2012 year</span><span class="c2" style="top:33px">Information 2</span>
    <span class="c1" style="top:52px">5000 sq.ft</span><span class="c2" style="top:52px">Information 3</span>
  </div>
  <div class="listing" style="top:94px">
    <div class="thumb" role="img" aria-label="House photo" style="background:linear-gradient(#8fb1d8,#a07c5a 55%,#5f7a3e)"></div>
    <span class="c1" style="top:15px">Villa</span><span class="c2" style="top:15px">Information 1</span>
    <span class="c1" style="top:33px">2012 year</span><span class="c2" style="top:33px">Information 2</span>
    <span class="c1" style="top:52px">5000 sq.ft</span><span class="c2" style="top:52px">Information 3</span>
  </div>
  <div class="listing" style="top:170px">
    <div class="thumb" role="img" aria-label="Glass tower photo" style="background:linear-gradient(135deg,#1f4f9a,#8fc0ea)"></div>
    <span class="c1" style="top:15px">Villa</span><span class="c2" style="top:15px">Information 1</span>
    <span class="c1" style="top:33px">2012 year</span><span class="c2" style="top:33px">Information 2</span>
    <span class="c1" style="top:52px">5000 sq.ft</span><span class="c2" style="top:52px">Information 3</span>
  </div>
</div>
<div class="abs badge">Home<br>for Sale</div>

<section class="abs search-band"></section>
<div class="abs search-map" role="img" aria-label="Folded world map"></div>
<div class="abs search-panel"></div>
<div class="abs search-title">Advanced Search</div>
<div class="abs select" style="left:263px">Search by Map</div>
<div class="abs select" style="left:380px">Search by&nbsp; MLS ID</div>
<div class="abs select" style="left:497px">Search by Price</div>
<div class="abs select" style="left:616px">Search by area</div>
<div class="abs btn" style="left:668px;top:523px;width:57px;height:20px;line-height:20px">Search</div>

<section class="abs showcase"></section>
<div class="abs section-title">Work Showcase</div>
<div class="abs rule"></div>
<div class="abs work" style="left:104px;width:154px;background:linear-gradient(135deg,#1d3f78,#6c93c6 50%,#3e4b3a)" role="img" aria-label="Glass office building at dusk"><div class="cap">Lorem ipsum dolor sit amet, consectetur adipisicing elit</div></div>
<div class="abs work" style="left:271px;width:155px;background:linear-gradient(90deg,#6a3a22,#c9a27c 50%,#e9e4dc)" role="img" aria-label="Interior staircase"><div class="cap">Lorem ipsum dolor sit amet, consectetur adipisicing elit</div></div>
<div class="abs work" style="left:441px;width:156px;background:linear-gradient(#3e6fc4,#9ab9e3 45%,#a08064 65%,#5b7a37)" role="img" aria-label="Suburban houses"><div class="cap">Lorem ipsum dolor sit amet, consectetur adipisicing elit</div></div>
<div class="abs work" style="left:610px;width:155px;background:linear-gradient(#7ea7d8,#e4e4e0 45%,#4e7a34)" role="img" aria-label="White house with garden"><div class="cap">Lorem ipsum dolor sit amet, consectetur adipisicing elit</div></div>
<div class="abs pager">Previous 1 2 3 4 5 6 7 8 Next</div>
<div class="abs pager-rule"></div>

<div class="abs col" style="left:107px">
  <h2>Welcome To <b>LAKE VORISSA</b></h2>
  <p>Lorem ipsum dolor sit amet, consectetur adipisicing elit, sed do eiusmod tempor incididunt ut labore et dolore magna aliqua. Ut enim ad minim veniam, quis nostrud exercitation ullamco laboris nisi ut aliquip ex ea commodo consequat. Duis aute irure dolor in reprehenderit in voluptate velit esse cillum dolore eu fugiat nulla pariatur. Excepteur sint occaecat cupidatat non proident, sunt in culpa qui officia deserunt mollit anim id est laborum.</p>
  <p class="lead">Lorem ipsum dolor sit amet, consectetur adipisicing elit.</p>
</div>
<div class="abs divider" style="left:318px"></div>
<div class="abs col" style="left:335px">
  <h2>Blog....</h2>
  <p>Lorem ipsum dolor sit amet, consectetur adipisicing elit, sed do eiusmod tempor incididunt ut labore et dolore magna aliqua.</p><span class="more">more</span>
  <p>Lorem ipsum dolor sit amet, consectetur adipisicing elit, sed do eiusmod tempor incididunt ut labore et dolore magna aliqua.</p><span class="more">more</span>
  <p>Lorem ipsum dolor sit amet, consectetur adipisicing elit, sed do eiusmod tempor incididunt ut labore et dolore magna aliqua.</p><span class="more">more</span>
</div>
<div class="abs divider" style="left:547px"></div>
<div class="abs col" style="left:562px">
  <h2>News....</h2>
  <p>Lorem ipsum dolor sit amet, consectetur adipisicing elit, sed do eiusmod tempor incididunt ut labore et dolore magna aliqua.</p><span class="more">more</span>
  <p>Lorem ipsum dolor sit amet, consectetur adipisicing elit, sed do eiusmod tempor incididunt ut labore et dolore magna aliqua.</p><span class="more">more</span>
  <p>Lorem ipsum dolor sit amet, consectetur adipisicing elit, sed do eiusmod tempor incididunt ut labore et dolore magna aliqua.</p><span class="more">more</span>
</div>

<footer class="abs footer"></footer>
<div class="abs features">
  <div class="foot-title">Key Features</div>
  <ul>
    <li>Lorem ipsum dolor sit amet, consectetur adipisicing elit</li>
    <li>Lorem ipsum dolor sit amet, consectetur adipisicing elit</li>
    <li>Lorem ipsum dolor sit amet, consectetur adipisicing elit</li>
    <li>Lorem ipsum dolor sit amet, consectetur adipisicing elit</li>
    <li>Lorem ipsum dolor sit amet, consectetur adipisicing elit</li>
    <li>Lorem ipsum dolor sit amet, consectetur adipisicing elit</li>
  </ul>
</div>
<div class="abs vline" style="left:352px"></div>
<div class="abs foot-title offices">Our Office Locations</div>
<div class="abs office-map" role="img" aria-label="World map with office markers"></div>
<ul class="abs places" style="left:398px;top:1073px"><li>Place 1</li><li>Place 2</li><li>Place 3</li></ul>
<ul class="abs places" style="left:492px;top:1073px"><li>Place 1</li><li>Place 2</li><li>Place 3</li></ul>
<div class="abs vline" style="left:578px"></div>
<div class="abs social" style="top:987px"><i style="background:#4aa6d8"></i><span>Follow us on Chirpline</span></div>
<div class="abs social" style="top:1015px"><i style="background:#3c64ad"></i><span>Login to Friendloop</span></div>
<div class="abs social" style="top:1046px;height:29px"><i style="background:#2f78b4"></i><span class="two">Connect with us<br>on Proflink</span></div>
<div class="abs social" style="top:1078px;border:0"><i style="background:var(--orange)"></i><span class="two">Send us your<br>email enquiries</span></div>

<div class="abs bottom"></div>
<div class="abs bottom-links">HOME | COMPANY | ASSOCIATES | SEARCH PROPERTIES | MARKETING &amp; DESIGN | CONTACT</div>
<div class="abs copyright">Copyright All right reserved</div>

</body>
</html>
```